Business card for dental office with laser therapy / dental facial esthetic

A simple logo which should signifies
Dentistry intraoral as primary and with extended extraoral cosmetic facial esthetic services ( regenerative skincare ) which enhance Beauty as whole .
Conservative high tech approach by using laser intraoral and extraoral limited to face and neck
Front Face :May be black background with neon blue / purplish Rim signifies laser ( ?) & abstract face profile and tooth or Apple design in one ? / see upload inspiration design
Back side : simple appointment slots with date and time / white background / black letter

Color : black/ neon blue/ purplish and gold incorporate for logo design
Final design : dental / esthetic / modern high tech and safe

Target Market(s)

Dental Patients who seeks more high end cosmetic treatment

Industry/Entity Type

Health Care

Contact Information for Business Card

Esthetic modern elegant looking
Logo and office must haves important informations

Logo Text

Family & Cosmetic Dentistry

Font styles to use
Script

Requirements
Must have
• Name of practice and all important informations
• Family & Cosmetic Dentistry
• Lan B. Orsova DMD,PC
• 48302 Bramcote Lane ,ste.217
• Kettle Ridge ,VA 20931
• Ph. 555-308-7291
• Fax 555-3087295
Nice to have
• More abstract
• Front : black back ground with neon blue rim (signifies laser therapy)
• Logo can also be golden gold / neon blue
• Address & Infos can be white
Should not have
• Not to busy looking

```html
<!DOCTYPE html>
<html lang="en">
<head>
<meta charset="utf-8">
<title>Orsova Dental – Business Card</title>
<link href="https://fonts.googleapis.com/css2?family=Archivo+Narrow:wght@600;700&family=Playfair+Display:wght@400&display=swap" rel="stylesheet">
<style>
  :root {
    --backdrop: #cfcfcf;
    --charcoal: #333132;
    --white: #ffffff;
    --ink: #111111;
    --tooth-blue: #3db8ec;
    --strip-1: #0396dc;
    --strip-2: #0280c8;
    --strip-3: #0266b3;
    --row-1: #efeff0;
    --row-2: #e4e4e6;
    --row-3: #d4d4d6;
    --fold: #0a55a6;
    --back-light: #00a3e4;
    --back-mid: #0479c4;
    --back-dark: #0057a8;
  }
  * { margin: 0; padding: 0; box-sizing: border-box; }
  html, body { width: 1200px; height: 1200px; overflow: hidden; }
  body { background: var(--backdrop); position: relative; }

  .card { position: absolute; left: 199px; width: 822px; height: 502px; overflow: visible; }

  /* Front */
  .card-front { top: 22px; background: var(--white); }
  .identity-panel { position: absolute; left: 0; top: 0; width: 418px; height: 502px; background: var(--charcoal); }
  .brand-mark { position: absolute; left: 0; width: 418px; top: 200px; display: flex; align-items: center; justify-content: center; gap: 12px; }
  .brand-mark .dot { width: 22px; height: 22px; border-radius: 50%; background: var(--tooth-blue); }
  .brand-name { font-family: "Playfair Display", serif; font-size: 34px; color: var(--tooth-blue); }
  .practice-name { position: absolute; left: 0; width: 418px; top: 340px; text-align: center; font-family: "Playfair Display", serif; font-size: 22px; letter-spacing: 0.5px; color: var(--white); transform: scaleX(0.88); }

  .fold { position: absolute; left: 391px; width: 27px; height: 23px; background: var(--fold); }
  .fold-top { top: 90px; clip-path: polygon(100% 0, 100% 100%, 0 100%); }
  .fold-bottom { top: 389px; clip-path: polygon(0 0, 100% 0, 100% 100%); }

  .contact-list { position: absolute; left: 391px; top: 113px; width: 431px; }
  .contact-row { display: flex; height: 92px; }
  .contact-row:first-child { height: 93px; }
  .contact-icon { width: 98px; display: flex; align-items: center; justify-content: center; }
  .contact-text { flex: 1; display: flex; flex-direction: column; justify-content: center; padding-left: 22px; font-family: "Archivo Narrow", sans-serif; font-weight: 700; color: var(--ink); }
  .row-address .contact-icon { background: var(--strip-1); }
  .row-address .contact-text { background: var(--row-1); font-size: 22px; line-height: 1.4; }
  .row-phone .contact-icon { background: var(--strip-2); }
  .row-phone .contact-text { background: var(--row-2); font-size: 32px; }
  .row-fax .contact-icon { background: var(--strip-3); }
  .row-fax .contact-text { background: var(--row-3); font-size: 32px; }

  /* Back */
  .card-back { top: 574px; background: radial-gradient(ellipse at 50% 70%, var(--back-light) 0%, var(--back-mid) 45%, var(--back-dark) 100%); }
  .emblem-disc { position: absolute; left: 292px; top: 68px; width: 238px; height: 238px; border-radius: 50%; background: var(--white); display: flex; align-items: center; justify-content: center; }
  .emblem-disc .brand-name { font-size: 30px; color: var(--back-mid); }
  .slot { position: absolute; top: 376px; }
  .slot-label { font-family: "Playfair Display", serif; font-size: 20px; color: var(--ink); line-height: 1; transform: scaleX(0.9); transform-origin: left; }
  .slot-box { margin-top: 4px; width: 150px; height: 51px; background: var(--white); border: 1px solid var(--back-dark); }
  .slot-date { left: 68px; }
  .slot-time { left: 636px; }
  .appointment-title { position: absolute; left: 0; width: 822px; top: 400px; text-align: center; font-family: "Playfair Display", serif; font-size: 30px; color: var(--ink); transform: scaleX(0.9); }
</style>
</head>
<body>

<section class="card card-front">
  <div class="identity-panel">
    <div class="brand-mark"><span class="dot"></span><span class="brand-name">Orsova Dental</span></div>
    <p class="practice-name">LAN B. ORSOVA DMD,PC</p>
  </div>
  <div class="fold fold-top"></div>
  <div class="fold fold-bottom"></div>
  <div class="contact-list">
    <div class="contact-row row-address">
      <div class="contact-icon">
        <svg width="36" height="48" viewBox="0 0 36 48" aria-hidden="true"><path d="M18 2C9 2 2 9 2 18c0 10 16 28 16 28s16-18 16-28C34 9 27 2 18 2z" fill="#fff"/><circle cx="18" cy="17" r="6" fill="var(--strip-1)"/></svg>
      </div>
      <div class="contact-text"><span>Bramcote Lane ste217 48302</span><span>Kettle Ridge , VA 20931</span></div>
    </div>
    <div class="contact-row row-phone">
      <div class="contact-icon">
        <svg width="26" height="46" viewBox="0 0 26 46" aria-hidden="true"><rect x="1" y="1" width="24" height="44" rx="3" fill="#fff"/><rect x="4" y="6" width="18" height="30" fill="var(--strip-2)"/><circle cx="13" cy="40" r="2" fill="var(--strip-2)"/></svg>
      </div>
      <div class="contact-text">555-308-7291</div>
    </div>
    <div class="contact-row row-fax">
      <div class="contact-icon">
        <svg width="40" height="40" viewBox="0 0 40 40" aria-hidden="true"><path d="M10 2h14l6 6v8H10z" fill="#fff"/><rect x="2" y="16" width="36" height="16" rx="3" fill="#fff"/><rect x="8" y="24" width="24" height="14" fill="#fff" stroke="var(--strip-3)" stroke-width="2"/><path d="M12 29h10M12 33h10" stroke="var(--strip-3)" stroke-width="2"/><rect x="24" y="28" width="5" height="6" fill="var(--strip-3)"/></svg>
      </div>
      <div class="contact-text">555-3087295</div>
    </div>
  </div>
</section>

<section class="card card-back">
  <div class="emblem-disc"><span class="brand-name">Orsova Dental</span></div>
  <div class="slot slot-date"><p class="slot-label">DATE</p><div class="slot-box"></div></div>
  <p class="appointment-title">APPOINTMENT</p>
  <div class="slot slot-time"><p class="slot-label">TIME</p><div class="slot-box"></div></div>
</section>

</body>
</html>
```